Basic / Quick Business Card

Quick easy design project!

Need a one sided basic business card that matches font & style of brand and bottle label for our gourmet condiment, Brindle Harrow Sauce. Brindle Harrow Sauce is sold in specialty retail, gourmet groceries and appears on chef-driven restaurant menus, so the target market is a high end, gourmet, artisan-made food-loving customer.

Files Included:
Sauce Bottle Label
Brindle Harrow Sauce Round Logos

**About the logos - the logo may be used in a circle or alone vertically as on side of the bottle label**

Layout of Card:
May be vertical or horizontal based on designer ideas.

Logo usage (in circle vs. stand alone vertical logo) is up to designers descretion as well.

Reverse side of business card will be various high end / professional product photos / food shots using us.kelbo.com system. **Designer on this project will NOT design a reserve for the card.**

Paper that will be used for printing:
Kelbo Standard - it's a WHITE paper, but we use a cream background on Brindle Harrow Sauce branding, so please take this into account on design to stay brand consistent.

Elements & Copy for Card:
1. Logo in either script horizontal or vertical version
2. Copy: "Artisan Made - Small Batch"
3. Name - Wes Dorrance
4. Title - Creator
5. Phone - xxx.xxx.xxxx
6. xxxx@brindleharrow.com
7. URL: brindleharrowsauce.com
8. Social Media: @getbrindleharrow on Quillo / Pagora / Lumigrid

Please provide final files in Illustrator or InDesign format.

```html
<!DOCTYPE html>
<html lang="en">
<head>
<meta charset="utf-8">
<title>Brindle Harrow Sauce — Business Card</title>
<link rel="stylesheet" href="https://fonts.googleapis.com/css2?family=Special+Elite&display=swap">
<style>
  :root {
    --ink: #231f20;
    --amber: #e8a11a;
    --cream: #efeedc;
    --backdrop: #e9e6e6;
    --type: "Special Elite", "Courier New", monospace;
  }
  * { box-sizing: border-box; margin: 0; padding: 0; }
  html, body {
    width: 1200px; height: 867px; overflow: hidden;
    background: var(--backdrop);
    font-family: var(--type);
  }
  .card {
    position: absolute; left: 100px; top: 146px;
    width: 1000px; height: 574px;
    background: var(--ink);
    padding: 11px;
  }
  .card-band {
    width: 100%; height: 100%;
    background: var(--amber);
    padding: 17px;
  }
  .card-inner {
    width: 100%; height: 100%;
    background: var(--ink);
    padding: 11px;
  }
  .card-face {
    position: relative;
    width: 100%; height: 100%;
    background: var(--cream);
    color: var(--ink);
  }
  /* face is offset 39px from card edge */
  .dash-frame {
    position: absolute;
    left: 16px; right: 17px; top: 30px; bottom: 18px;
    border: 3px dashed var(--amber);
  }
  .dash-divider {
    position: absolute;
    left: 16px; right: 17px; top: 385px;
    border-top: 3px dashed var(--amber);
  }
  .tagline {
    position: absolute; right: 26px; top: 18px;
    padding: 0 8px;
    background: var(--cream);
    font-size: 20px; font-weight: bold; letter-spacing: 0.5px;
    -webkit-text-stroke: 0.5px var(--ink);
  }
  .brand {
    position: absolute; left: 0; right: 0; top: 86px;
    text-align: center;
    color: var(--ink);
  }
  .brand-name {
    font-size: 62px; line-height: 62px;
    -webkit-text-stroke: 0.6px var(--ink);
  }
  .brand-sub {
    font-size: 22px; letter-spacing: 8px; margin-top: 6px;
  }
  .person {
    position: absolute; left: 0; right: 0; top: 314px;
    text-align: center;
    color: var(--amber);
    font-size: 29px;
    -webkit-text-stroke: 0.5px var(--amber);
  }
  .contact {
    position: absolute; left: 0; right: 0; top: 402px;
    text-align: center;
    font-size: 17px; font-weight: bold;
    -webkit-text-stroke: 0.3px var(--ink);
    white-space: nowrap;
  }
  .social {
    position: absolute; left: 0; right: 0; top: 446px;
    display: flex; justify-content: center;
  }
  .social-list {
    display: flex; gap: 26px; align-items: center;
    background: var(--cream);
    padding: 0 12px;
    font-size: 17px; font-weight: bold;
    -webkit-text-stroke: 0.3px var(--ink);
    list-style: none;
  }
  .social-item { display: flex; align-items: center; gap: 10px; }
  .social-mark {
    width: 20px; height: 20px; border-radius: 3px;
    background: var(--amber);
  }
</style>
</head>
<body>
  <div class="card">
    <div class="card-band">
      <div class="card-inner">
        <div class="card-face">
          <div class="dash-frame"></div>
          <div class="dash-divider"></div>
          <p class="tagline">Artisan Made - Small Batch</p>
          <div class="brand">
            <p class="brand-name">Brindle<br>Harrow</p>
            <p class="brand-sub">sauce</p>
          </div>
          <p class="person">Wes Dorrance | Creator</p>
          <p class="contact">P. 123.456.7890 | E. dorrance@brindleharrow.com | W. www.brindleharrowsauce.com</p>
          <div class="social">
            <ul class="social-list">
              <li class="social-item"><span class="social-mark" aria-label="Quillo"></span>@getbrindleharrow</li>
              <li class="social-item"><span class="social-mark" aria-label="Lumigrid"></span>getbrindleharrow</li>
              <li class="social-item"><span class="social-mark" aria-label="Pagora"></span>getbrindleharrow</li>
            </ul>
          </div>
        </div>
      </div>
    </div>
  </div>
</body>
</html>
```